SaaS Early tech startup business card design

Unique design for experience ecommerce platform company. the business cards will be used by executive members. conformance with color code is required.

```html
<!DOCTYPE html>
<html lang="en">
<head>
<meta charset="utf-8">
<title>Novalyn Business Card</title>
<link href="https://fonts.googleapis.com/css2?family=Montserrat:wght@700&family=Open+Sans:wght@400;600&display=swap" rel="stylesheet">
<style>
  :root {
    --ink-blue: #16668f;
    --deep-blue: #135b80;
    --teal: #12b59a;
    --white: #ffffff;
    --text: #1d2a33;
    --backdrop: #232323;
  }
  * { margin: 0; padding: 0; box-sizing: border-box; }
  html, body { width: 1200px; height: 988px; overflow: hidden; background: var(--backdrop); }
  .canvas { position: relative; width: 1200px; height: 988px; }
  .card {
    position: absolute; left: 250px; width: 700px; height: 400px;
    border-radius: 28px; overflow: hidden;
  }
  .card--front { top: 60px; background: var(--ink-blue); display: flex; align-items: center; justify-content: center; }
  .card--back { top: 528px; background: var(--white); }
  .wordmark {
    font-family: "Montserrat", sans-serif; font-weight: 700; color: var(--teal);
    letter-spacing: -1px; display: flex; align-items: center; gap: 14px;
  }
  .card--front .wordmark { font-size: 96px; }
  .wordmark__dot { width: 0.28em; height: 0.28em; background: var(--teal); border-radius: 50%; }
  .card--back .wordmark { position: absolute; left: 60px; top: 110px; font-size: 54px; gap: 10px; }
  .divider { position: absolute; left: 340px; top: 48px; width: 2px; height: 168px; background: var(--teal); }
  .contact { position: absolute; left: 364px; top: 36px; font-family: "Open Sans", sans-serif; color: var(--text); }
  .contact__name { font-family: "Montserrat", sans-serif; font-weight: 700; font-size: 26px; color: var(--ink-blue); line-height: 1.1; }
  .contact__role { font-size: 14px; line-height: 1.3; margin-bottom: 12px; }
  .contact__address { font-size: 14px; line-height: 1.35; margin-bottom: 10px; }
  .contact__list { list-style: none; font-size: 14px; line-height: 1.45; }
  .contact__list li { display: flex; align-items: center; gap: 8px; }
  .contact__list svg { width: 12px; height: 12px; fill: var(--ink-blue); }
  .wave { position: absolute; left: 0; top: 0; width: 700px; height: 400px; }
</style>
</head>
<body>
<main class="canvas">
  <section class="card card--front">
    <div class="wordmark"><span>Novalyn</span><span class="wordmark__dot"></span></div>
  </section>

  <section class="card card--back">
    <svg class="wave" viewBox="0 0 700 400" preserveAspectRatio="none">
      <path d="M0 338 C 220 328, 380 293, 500 243 C 590 205, 650 189, 700 185 L700 400 L0 400 Z" fill="var(--teal)"/>
      <path d="M0 347 C 220 337, 380 302, 500 252 C 590 214, 650 197, 700 192 L700 400 L0 400 Z" fill="var(--white)"/>
      <path d="M0 353 C 220 343, 380 308, 500 258 C 590 220, 650 202, 700 197 L700 400 L0 400 Z" fill="var(--ink-blue)"/>
    </svg>
    <div class="wordmark"><span>Novalyn</span><span class="wordmark__dot"></span></div>
    <div class="divider"></div>
    <div class="contact">
      <p class="contact__name">Daniel Reyes</p>
      <p class="contact__role">Managing Director</p>
      <p class="contact__address">Your location street here,<br>Country name, Country - 91542</p>
      <ul class="contact__list">
        <li><svg viewBox="0 0 12 12"><path d="M2.5 1 L4.5 1 L5.3 3.3 L4 4.4 C4.6 5.8 6.2 7.4 7.6 8 L8.7 6.7 L11 7.5 L11 9.5 C11 10.3 10.3 11 9.5 11 C5 11 1 7 1 2.5 C1 1.7 1.7 1 2.5 1 Z"/></svg>+012 345 6789</li>
        <li><svg viewBox="0 0 12 12"><path d="M1 3 L11 3 L11 10 L1 10 Z M1.6 3.5 L6 7 L10.4 3.5" stroke="#fff" stroke-width="0.8"/></svg>info@youremail.com</li>
        <li><svg viewBox="0 0 12 12"><circle cx="6" cy="6" r="5"/></svg>www.yourwebsite.com</li>
      </ul>
    </div>
  </section>
</main>
</body>
</html>
```